Corbeck Aluminium Design Upgrade

- This is for a layout design of the home page only. No coding required.

- The design should be based around the attached HPID (home page information design) I've attached both a JPEG of this
- Information only is in RED text. Copy to go on the design in BLACK text. Some instructions are in the HPID. Please be creative!
- The design needs to be clean and spacious
- Use the logo provided. Please use the colours from the logos in the website design.
- I've attached some images to use as examples to use for home page gallery
- The product logos (Pelvane, Trimbough etc) showed in the HPV can be googled for a higher quality image if required.
- The header can be changed/altered - just needs to have all information as per logo, along with the phone number.

- Expected standard of design examples: (Please DO NOT copy these exactly – they are just examples)
http://www.halden-works.example.nz/
http://www.plinthcove.example.nz/
http://www.dusofern.example.nz/

Width of content will be 1100 pixels when implemented as a web page. Header height (without nav bar) 150-160 pixels.

The winning PSD file will have to be provided as follows…
1. Canvas size of 2000px x 2000px - 72ppi in Adobe Photoshop (CS5 compatible)
2. Width of content section is 1100px wide - centered in the canvas
3. Any button rollovers/hovers in the PSD as hidden layers.
4. All fonts used must be Google fonts (except for the header fonts).
5. You will need to supply the chosen home page plus one example page (example page as a style guide for how all other pages will look). Example page is only the header and navigational bar at the top, an empty sector in the middle with a column (180 px wide) which can be left or right aligned which means the main sector is 920 pixels wide, and then the footer at the bottom of the page.

```html
<!DOCTYPE html>
<html lang="en">
<head>
<meta charset="utf-8">
<title>Corbeck Aluminium – Home</title>
<link href="https://fonts.googleapis.com/css2?family=Oswald:wght@400;500;700&family=Open+Sans:wght@400;600;700&display=swap" rel="stylesheet">
<style>
:root{
  --navy:#161a6b;
  --red:#ee1c24;
  --yellow:#f6e21a;
  --white:#ffffff;
  --text:#6b6b6b;
  --footer:#262626;
  --footer-base:#1b1b1b;
  --gold:#e6a614;
  --logo-grey:#d8d8d8;
}
*{margin:0;padding:0;box-sizing:border-box}
html,body{width:697px;height:1200px;overflow:hidden;background:var(--white)}
body{font-family:"Open Sans",Arial,sans-serif;color:var(--text);position:relative}
.abs{position:absolute}

/* header */
.site-header{left:0;top:0;width:697px;height:75px;background:var(--navy)}
.brand{left:72px;top:7px;width:100px;height:56px;display:flex;align-items:center;gap:5px}
.brand-square{width:12px;height:12px;background:var(--red);flex:none}
.brand-name{font-weight:700;font-size:11px;line-height:13px;color:var(--white)}
.header-contact{left:288px;top:9px;width:220px;text-align:center;color:var(--white)}
.header-contact .place{font-size:8px;font-weight:600;letter-spacing:.3px}
.header-contact .phone{font-family:"Oswald",sans-serif;font-size:22px;font-weight:500;color:var(--red);line-height:27px}
.excellence{left:289px;top:45px;width:220px;height:11px;background:var(--yellow);font-size:7px;font-weight:700;color:var(--navy);line-height:11px;padding-left:8px;letter-spacing:.4px;white-space:nowrap}
.excellence span{background:var(--navy);color:var(--white);padding:0 4px;margin-left:4px}
.header-side{left:562px;top:16px;width:100px;text-align:right;color:var(--white);font-size:9px;line-height:13px}
.header-side .phone{font-size:10px;font-weight:600;margin-top:8px}

/* nav */
.main-nav{left:0;top:75px;width:697px;height:34px;background:var(--red);display:flex;align-items:center;padding-left:78px;gap:13px;white-space:nowrap}
.main-nav a{color:var(--white);font-size:8px;text-decoration:none;white-space:nowrap}

/* hero */
.hero{left:0;top:109px;width:697px;height:244px;background:linear-gradient(180deg,#b9c4cf 0%,#d7dbdf 35%,#a9aaa7 70%,#4f6a2e 100%)}
.hero-title{left:72px;top:166px;font-family:"Oswald",sans-serif;font-size:26px;font-weight:500;line-height:30px;color:var(--white)}
.hero-text{left:72px;top:200px;width:200px;font-size:8.5px;line-height:11px;color:var(--white)}
.btn-quote{left:72px;top:259px;width:82px;height:30px;background:var(--red);color:var(--white);font-family:"Oswald",sans-serif;font-size:11px;display:flex;align-items:center;justify-content:center;border-radius:3px}
.dots{left:344px;top:334px;display:flex;gap:5px}
.dots i{width:4px;height:4px;border-radius:50%;background:var(--white);opacity:.6}
.dots i:first-child{opacity:1}

/* partners */
.partners{left:72px;top:378px;width:548px;height:50px;display:flex;justify-content:space-between;align-items:center}
.partner{background:var(--logo-grey)}

/* products */
.card{width:174px}
.card-title{height:31px;background:var(--red);color:var(--white);font-weight:600;font-size:12px;line-height:31px;padding-left:10px;white-space:nowrap}
.card-image{height:100px;margin-top:6px}
.card-text{margin-top:12px;font-size:8px;line-height:11px;color:var(--text)}
.card-text p+p{margin-top:11px}
.img-blue{background:linear-gradient(180deg,#cfd9e2,#7f8f9a 60%,#5b6a4a)}
.img-white{background:linear-gradient(180deg,#dfe3e6,#b8bcbe 60%,#6f7d55)}
.img-dark{background:linear-gradient(180deg,#9eb0bf,#3d4650 55%,#8a8f8c)}

/* footer */
.site-footer{left:0;top:1059px;width:697px;height:110px;background:var(--footer)}
.footer-base{left:0;top:1169px;width:697px;height:31px;background:var(--footer-base)}
.footer-h{font-size:11px;font-weight:700;color:var(--white)}
.footer-list{list-style:none;font-size:8px;line-height:13px;color:#e0e0e0;white-space:nowrap}
.copyright{left:72px;top:1180px;font-size:7px;color:#8a8a8a}
.social{left:558px;top:1177px;display:flex;gap:6px}
.social i{width:13px;height:13px;border:1px solid #8a8a8a;border-radius:50%}
.badge{left:464px;top:1077px;width:67px;height:67px;border-radius:50%;background:radial-gradient(circle,#f6cf4a 0 55%,var(--gold) 56%)}
.guarantee{left:540px;top:1090px;width:95px;font-size:8px;line-height:11px;color:var(--white)}
</style>
</head>
<body>

<header class="abs site-header" aria-label="Site header">
  <div class="abs brand"><span class="brand-square"></span><span class="brand-name">Corbeck Aluminium</span></div>
  <div class="abs header-contact">
    <div class="place">UPPER HUNT , WELLINGTON</div>
    <div class="phone">(04) 555 0192</div>
  </div>
  <div class="abs excellence">EXCELLENCE <span>IN ALUMINIUM WINDOWS &amp; DOORS</span></div>
  <div class="abs header-side">Upper Hutt<br>Wellington<div class="phone">(04)555 0192</div></div>
</header>

<nav class="abs main-nav">
  <a>Home</a><a>About Us</a><a>Commercial</a><a>New Homes</a><a>Replacement Joinery</a><a>Double Glazing</a><a>Conservatories</a><a>Gallery</a><a>Get a Free Quote</a><a>Contact</a>
</nav>

<section class="abs hero" role="img" aria-label="Modern two-storey building with aluminium-framed glazing"></section>
<h1 class="abs hero-title">INNOVATIVE</h1>
<p class="abs hero-text">From small bays to large complex systems, Halden Works offer the design, Services and expertise to ensure your storage facilities improve your business' workflow.</p>
<a class="abs btn-quote">Get Free Quote</a>
<div class="abs dots"><i></i><i></i><i></i></div>

<section class="abs partners" aria-label="Partner brands">
  <div class="partner" style="width:70px;height:32px"></div>
  <div class="partner" style="width:72px;height:30px;border-radius:50%"></div>
  <div class="partner" style="width:70px;height:14px"></div>
  <div class="partner" style="width:46px;height:46px;border-radius:50%"></div>
  <div class="partner" style="width:72px;height:14px"></div>
  <div class="partner" style="width:46px;height:46px;border-radius:50%"></div>
</section>

<article class="abs card" style="left:72px;top:445px">
  <h2 class="card-title">New Homes</h2>
  <div class="card-image img-blue" role="img" aria-label="Glass conservatory on a new home"></div>
  <div class="card-text"><p>Sed ut perspiciatis unde omnis iste natus error sit voluptatem accusantium doloremque laudantium, totam rem aperiam, eaque ipsa quae ab illo inventore veritatis et quasi architecto beatae vitae dicta sunt explicabo.</p><p>Nemo enim ipsam voluptatem quia voluptas sit aspernatur aut odit aut fugit, sed quia consequuntur magni dolores eos qui ratione voluptatem sequi nesciunt.</p></div>
</article>
<article class="abs card" style="left:261px;top:445px">
  <h2 class="card-title">Commercial</h2>
  <div class="card-image img-white" role="img" aria-label="Commercial building with balcony glazing"></div>
  <div class="card-text"><p>Sed ut perspiciatis unde omnis iste natus error sit voluptatem accusantium doloremque laudantium, totam rem aperiam, eaque ipsa quae ab illo inventore veritatis et quasi architecto beatae vitae dicta sunt explicabo.</p><p>Nemo enim ipsam voluptatem quia voluptas sit aspernatur aut odit aut fugit, sed quia consequuntur magni dolores eos qui ratione voluptatem sequi nesciunt.</p></div>
</article>
<article class="abs card" style="left:448px;top:445px">
  <h2 class="card-title">Replacement Joinery</h2>
  <div class="card-image img-white" role="img" aria-label="House with replacement aluminium windows"></div>
  <div class="card-text"><p>Sed ut perspiciatis unde omnis iste natus error sit voluptatem accusantium doloremque laudantium, totam rem aperiam, eaque ipsa quae ab illo inventore veritatis et quasi architecto beatae vitae dicta sunt explicabo.</p><p>Nemo enim ipsam voluptatem quia voluptas sit aspernatur aut odit aut fugit, sed quia consequuntur magni dolores eos qui ratione voluptatem sequi nesciunt.</p></div>
</article>
<article class="abs card" style="left:148px;top:755px">
  <h2 class="card-title">Double Glazing</h2>
  <div class="card-image img-dark" role="img" aria-label="Double glazed window wall"></div>
  <div class="card-text"><p>Sed ut perspiciatis unde omnis iste natus error sit voluptatem accusantium doloremque laudantium, totam rem aperiam, eaque ipsa quae ab illo inventore veritatis et quasi architecto beatae vitae dicta sunt explicabo.</p><p>Nemo enim ipsam voluptatem quia voluptas sit aspernatur aut odit aut fugit, sed quia consequuntur magni dolores eos qui ratione voluptatem sequi nesciunt.</p></div>
</article>
<article class="abs card" style="left:380px;top:755px">
  <h2 class="card-title">Conservation</h2>
  <div class="card-image img-blue" role="img" aria-label="Building front with conservatory windows"></div>
  <div class="card-text"><p>Sed ut perspiciatis unde omnis iste natus error sit voluptatem accusantium doloremque laudantium, totam rem aperiam, eaque ipsa quae ab illo inventore veritatis et quasi architecto beatae vitae dicta sunt explicabo.</p><p>Nemo enim ipsam voluptatem quia voluptas sit aspernatur aut odit aut fugit, sed quia consequuntur magni dolores eos qui ratione voluptatem sequi nesciunt.</p></div>
</article>

<footer>
  <div class="abs site-footer"></div>
  <h3 class="abs footer-h" style="left:72px;top:1070px">Information</h3>
  <ul class="abs footer-list" style="left:72px;top:1089px"><li>Home</li><li>About Us</li><li>Commercial</li><li>New Homes</li><li>Replacement Joinery</li></ul>
  <ul class="abs footer-list" style="left:166px;top:1089px"><li>Double Glazing</li><li>Conservatories</li><li>Gallery</li><li>Get a Free Quote</li><li>Contact Us</li></ul>
  <h3 class="abs footer-h" style="left:275px;top:1070px">Contact Details</h3>
  <ul class="abs footer-list" style="left:275px;top:1089px"><li>PHONE NO : 045550192</li><li>FAX NO : 045550387</li><li>NEIL : 021 555 0716</li><li>Physical Address : 14 Harlow Cres, Upper Hutt</li><li>Postal address : PO Box 40213, Upper Hutt</li></ul>
  <div class="abs badge" aria-hidden="true"></div>
  <p class="abs guarantee">We Guarantee all our work. If there is ever a problem, we will be back to provide a solution</p>
  <div class="abs footer-base"></div>
  <p class="abs copyright">© 2014 Corbeck Aluminium Ltd , All Rights Reserved</p>
  <div class="abs social"><i></i><i></i><i></i><i></i></div>
</footer>

</body>
</html>
```